Business card design for Korvane Engineering Tandem

We need a new business card design along with all the necessary to place an order. The company is Korvane Engineering Tandem and we recently updated our logo.

```html
<!DOCTYPE html>
<html lang="en">
<head>
<meta charset="UTF-8">
<title>Korvane Engineering Tandem – Business Card</title>
<link rel="stylesheet" href="https://fonts.googleapis.com/css2?family=Montserrat:wght@400;500;700&display=swap">
<style>
  :root {
    --page-bg: #2b2b2d;
    --card-front: #8f8f90;
    --card-front-text: #cfcfd1;
    --card-back: #ffffff;
    --accent: #e0b40c;
    --ink: #1d1d1f;
  }
  * { box-sizing: border-box; margin: 0; padding: 0; }
  html, body {
    width: 1200px; height: 874px; overflow: hidden;
    background: var(--page-bg);
    font-family: "Montserrat", sans-serif;
  }
  .stage {
    position: relative; width: 1200px; height: 874px;
    display: flex; flex-direction: column; align-items: center; justify-content: center; gap: 40px;
  }
  .card {
    width: 560px; height: 320px; border-radius: 22px;
    position: relative; overflow: hidden;
  }
  .card--front {
    background: var(--card-front);
    display: flex; align-items: center; justify-content: center; gap: 14px;
    padding: 0 40px;
  }
  .brand-mark {
    width: 18px; height: 18px; background: var(--card-front-text); flex: none;
  }
  .brand-name {
    color: var(--card-front-text); font-weight: 700; font-size: 24px;
    letter-spacing: 1px; text-transform: uppercase; white-space: nowrap;
  }
  .card--back { background: var(--card-back); }
  .contact-block {
    position: absolute; left: 0; right: 0; top: 186px;
    display: flex; justify-content: center; align-items: stretch; gap: 14px;
  }
  .person { text-align: right; padding-top: 2px; }
  .person__name { color: var(--accent); font-weight: 700; font-size: 22px; line-height: 1.1; }
  .person__role { color: var(--ink); font-size: 14px; margin-top: 4px; }
  .divider { width: 1.5px; background: var(--accent); }
  .details { list-style: none; display: flex; flex-direction: column; gap: 6px; }
  .details li { display: flex; align-items: center; gap: 8px; font-size: 14px; color: var(--ink); white-space: nowrap; }
  .details svg { width: 12px; height: 12px; fill: var(--accent); flex: none; }
</style>
</head>
<body>
<main class="stage">
  <section class="card card--front" aria-label="Card front">
    <span class="brand-mark"></span>
    <span class="brand-name">Korvane Engineering Tandem</span>
  </section>

  <section class="card card--back" aria-label="Card back">
    <div class="contact-block">
      <div class="person">
        <p class="person__name">Marco Lindqvist</p>
        <p class="person__role">Managing Director</p>
      </div>
      <span class="divider"></span>
      <ul class="details">
        <li>
          <svg viewBox="0 0 24 24"><path d="M6.6 10.8a15 15 0 0 0 6.6 6.6l2.2-2.2c.3-.3.7-.4 1-.2 1.1.4 2.3.6 3.6.6.6 0 1 .4 1 1V20c0 .6-.4 1-1 1A17 17 0 0 1 3 4c0-.6.4-1 1-1h3.5c.6 0 1 .4 1 1 0 1.3.2 2.5.6 3.6.1.3 0 .7-.2 1z"/></svg>
          (555)214-7730
        </li>
        <li>
          <svg viewBox="0 0 24 24"><path d="M2 6l10 7 10-7v12H2z"/><path d="M2 4h20l-10 7z"/></svg>
          hello@korvanetandem.com
        </li>
        <li>
          <svg viewBox="0 0 24 24"><circle cx="12" cy="12" r="10"/></svg>
          www.korvanetandem.com
        </li>
      </ul>
    </div>
  </section>
</main>
</body>
</html>
```